larkforge website

commerce website to sell cookeries, brackets, mailboxes and to show off homes built. Modern Steel in design see marlo cycles web page to be like: https://www.marlocycles-demo.com/en/ sorry its bright nest hosting word press divi

must be able to add products to page

Target Market(s)

mainly western states of U.S.

Industry/Entity Type

Building Product

Coding

Coded - Design and coding required

Number of Pages Required

3 page

Font styles to use
Sans Serif

Colors

Designer to choose colors to be used in the design.

Requirements
Must have
• customers to be able to order products from page
• bright nest hosting word press divi

```html
<!DOCTYPE html>
<html lang="en">
<head>
<meta charset="utf-8">
<title>Larkforge</title>
<link href="https://fonts.googleapis.com/css2?family=Poppins:wght@400;500;600&family=Roboto+Condensed:ital,wght@1,700&display=swap" rel="stylesheet">
<style>
:root{
  --navy:#3e4a7c;
  --navy-mid:#5a6593;
  --navy-deep:#2b3256;
  --ink:#2f3342;
  --text:#555b66;
  --paper:#ffffff;
  --mist:#eef0f4;
  --line:#cfd3dc;
}
*{box-sizing:border-box;margin:0;padding:0}
html,body{width:742px;height:1200px;overflow:hidden}
body{font-family:"Poppins",sans-serif;background:var(--paper);color:var(--text);position:relative}
.site-header{position:absolute;top:0;left:0;width:742px;height:74px;background:var(--navy);color:#fff}
.brand{position:absolute;left:120px;top:14px;display:flex;align-items:center;gap:8px;font-weight:600;font-size:18px;letter-spacing:1px;text-transform:uppercase}
.brand-dot{width:14px;height:14px;border-radius:50%;background:#fff}
.top-contact{position:absolute;right:110px;top:10px;display:flex;gap:22px;font-size:8px;opacity:.9}
.top-contact span{display:flex;align-items:center;gap:4px}
.main-nav{position:absolute;right:110px;top:42px;display:flex;gap:26px;font-size:10px}
.main-nav a{color:#fff;text-decoration:none;padding-bottom:5px}
.main-nav a.active{border-bottom:2px solid #fff}
.hero{position:absolute;top:74px;left:0;width:742px;height:329px;background:linear-gradient(180deg,#8fb1d6 0%,#b9cfe2 35%,#d8d4cc 55%,#6b7a52 80%,#4f6b35 100%)}
.hero-title{position:absolute;top:275px;left:0;width:100%;text-align:center;color:#fff;font-size:22px;font-weight:500;line-height:1.3;text-shadow:0 1px 4px rgba(0,0,0,.45)}
.products-head{position:absolute;top:440px;width:100%;text-align:center}
.products-head h2{font-size:26px;font-weight:500;color:var(--navy)}
.products-head .rule{width:60px;height:2px;background:var(--navy);margin:6px auto 10px}
.products-head p{font-size:9px;line-height:1.5;width:560px;margin:0 auto}
.product-grid{position:absolute;top:536px;left:86px;display:flex;gap:19px}
.product-card{width:174px;height:217px;background:#fff;box-shadow:0 2px 8px rgba(0,0,0,.18);text-align:center}
.product-photo{height:138px}
.photo-cookery{background:linear-gradient(160deg,#3a3d40,#8a8f93 55%,#2c2f33)}
.photo-brackets{background:linear-gradient(180deg,#9fbad6,#e9ecef 55%,#7b7f84)}
.photo-mailbox{background:linear-gradient(170deg,#c6c9cc,#4a4d52 60%,#9aa0a5)}
.product-card h3{font-size:12px;font-weight:500;color:var(--ink);margin-top:12px}
.product-card .rule{width:30px;height:1px;background:var(--line);margin:5px auto}
.product-card p{font-size:7.5px;line-height:1.45;padding:0 14px}
.shop-btn{position:absolute;top:773px;left:320px;width:100px;height:24px;border-radius:12px;background:var(--navy);color:#fff;font-size:9px;font-weight:600;text-align:center;line-height:24px;letter-spacing:.5px}
.goal{position:absolute;top:815px;left:0;width:742px;height:222px;background:var(--mist)}
.goal-mark{position:absolute;left:170px;top:10px;width:400px;height:200px;background:radial-gradient(ellipse at center,rgba(62,74,124,.12),rgba(62,74,124,0) 70%)}
.goal-line{position:absolute;left:130px;width:482px;height:1px;background:#9aa0b0}
.goal-icon{position:absolute;left:356px;top:48px}
.goal h2{position:absolute;top:98px;width:100%;text-align:center;font-family:"Roboto Condensed",sans-serif;font-style:italic;font-weight:700;font-size:23px;line-height:1.25;color:var(--ink);text-transform:uppercase}
.footer-nav{position:absolute;top:1057px;left:0;width:742px;height:35px;background:var(--navy-mid);display:flex;justify-content:center;align-items:center;gap:40px;font-size:9px;color:#fff}
.site-footer{position:absolute;top:1092px;left:0;width:742px;height:81px;background:var(--navy);color:#fff}
.site-footer .brand{left:115px;top:30px;font-size:16px}
.footer-contact{position:absolute;top:28px;font-size:8px;line-height:1.5;display:flex;gap:8px}
.footer-contact svg{margin-top:2px}
.social{position:absolute;right:115px;top:32px;display:flex;gap:5px}
.social span{width:16px;height:16px;border:1px solid #fff;border-radius:50%}
.copyright{position:absolute;top:1173px;left:0;width:742px;height:27px;background:var(--navy-deep);color:#dfe2ea;font-size:7.5px;text-align:center;line-height:27px}
</style>
</head>
<body>
<header class="site-header">
  <div class="brand"><span class="brand-dot"></span>Larkforge</div>
  <div class="top-contact">
    <span><svg width="8" height="8" viewBox="0 0 10 10"><path d="M2 1l2 2-1 1.5c.6 1.2 1.4 2 2.5 2.5L7 6l2 2-1.5 1.5C4 9 1 6 .5 2.5z" fill="#fff"/></svg>123.456.7890</span>
    <span><svg width="9" height="7" viewBox="0 0 10 8"><rect x=".5" y=".5" width="9" height="7" fill="none" stroke="#fff"/><path d="M.5 .5l4.5 4 4.5-4" fill="none" stroke="#fff"/></svg>inquiry@larkforge.com</span>
  </div>
  <nav class="main-nav">
    <a class="active">Home</a><a>Products</a><a>Home Built</a><a>About Us</a><a>Contact Us</a>
  </nav>
</header>

<section class="hero" role="img" aria-label="Photo of a large white two-storey home with green lawn and trees">
  <h1 class="hero-title">We Sell Cookeries, Brackets, Mailboxes And To Show<br>Off Homes Built</h1>
</section>

<section class="products-head">
  <h2>Our Products</h2>
  <div class="rule"></div>
  <p>Lorem ipsum dolor sit amet, consectetuer adipiscing elit, sed diam nonummy nibh euismod tincidunt ut laoreet dolore magna aliquam erat volutpat. Ut wisi enim ad minim.</p>
</section>

<div class="product-grid">
  <article class="product-card">
    <div class="product-photo photo-cookery" role="img" aria-label="Photo of a steel outdoor cookery unit"></div>
    <h3>Steel Cookery</h3><div class="rule"></div>
    <p>Lorem ipsum dolor sit amet, consectetuer adipiscing elit, sed diam</p>
  </article>
  <article class="product-card">
    <div class="product-photo photo-brackets" role="img" aria-label="Photo of a modern house with steel brackets"></div>
    <h3>Brackets</h3><div class="rule"></div>
    <p>Lorem ipsum dolor sit amet, consectetuer adipiscing elit, sed diam</p>
  </article>
  <article class="product-card">
    <div class="product-photo photo-mailbox" role="img" aria-label="Photo of a steel mailbox"></div>
    <h3>Mail Boxes</h3><div class="rule"></div>
    <p>Lorem ipsum dolor sit amet, consectetuer adipiscing elit, sed diam</p>
  </article>
</div>

<div class="shop-btn">SHOP NOW</div>

<section class="goal">
  <div class="goal-mark" role="img" aria-label="Faint brand decoration"></div>
  <div class="goal-line" style="top:62px"></div>
  <svg class="goal-icon" width="30" height="30" viewBox="0 0 30 30"><circle cx="15" cy="15" r="13" fill="var(--mist)" stroke="#3e4a7c" stroke-width="2"/><circle cx="15" cy="15" r="8" fill="none" stroke="#3e4a7c" stroke-width="2"/><circle cx="15" cy="15" r="3" fill="#3e4a7c"/></svg>
  <h2>Our goal is simply to build the best products<br>in the world</h2>
  <div class="goal-line" style="top:165px"></div>
</section>

<nav class="footer-nav"><span>Home</span><span>Products</span><span>Home Built</span><span>About Us</span><span>Contact Us</span></nav>

<footer class="site-footer">
  <div class="brand"><span class="brand-dot"></span>Larkforge</div>
  <div class="footer-contact" style="left:255px"><svg width="9" height="7" viewBox="0 0 10 8"><rect x=".5" y=".5" width="9" height="7" fill="none" stroke="#fff"/><path d="M.5 .5l4.5 4 4.5-4" fill="none" stroke="#fff"/></svg><div>Email Us<br>inquiry@larkforge.com</div></div>
  <div class="footer-contact" style="left:440px"><svg width="8" height="8" viewBox="0 0 10 10"><path d="M2 1l2 2-1 1.5c.6 1.2 1.4 2 2.5 2.5L7 6l2 2-1.5 1.5C4 9 1 6 .5 2.5z" fill="#fff"/></svg><div>Call On<br>123.456.7890</div></div>
  <div class="social"><span></span><span></span><span></span></div>
</footer>
<div class="copyright">Copyright © 2020 Larkforge. All Rights Reserved.</div>
</body>
</html>
```